Simplified minimalist but bold website

Design a website for a brand 'Brighten Every Day' that shares ideas to make managing home and health easier through email swap series, webinars and eventually courses.

Simple landing page to attract users to sign up for a freebie.

Target Market(s)

women with families & homes to run

Number of Pages Required

1 page

Font styles to use
Sans Serif

Colors
e667a6
b768aa
acd136
ffffff
959595

Requirements
Must have
• Simplified look, line icons, opt-in template, contact us form

```html
<!DOCTYPE html>
<html lang="en">
<head>
<meta charset="utf-8">
<title>Brighten Every Day</title>
<link href="https://fonts.googleapis.com/css2?family=Courier+Prime&family=Montserrat:wght@400;500;600;700&family=Open+Sans:wght@400;600&display=swap" rel="stylesheet">
<style>
:root{
  --pink:#e0489a;
  --pink-soft:#f6e0ed;
  --grey-bg:#f4f4f4;
  --grey-text:#959595;
  --ink:#2b2b2b;
  --footer:#2f2f2f;
  --white:#ffffff;
  --line:#d9d9d9;
}
*{box-sizing:border-box;margin:0;padding:0}
html,body{width:733px;height:1200px;overflow:hidden;background:var(--white)}
body{position:relative;font-family:"Open Sans",sans-serif;color:var(--ink)}
.top-bar{position:absolute;top:0;left:0;width:733px;height:3px;background:var(--pink);z-index:2}
.menu-btn{position:absolute;top:0;right:0;width:51px;height:41px;background:var(--pink);z-index:2;display:flex;align-items:center;justify-content:center}
.hero{position:absolute;top:0;left:0;width:733px;height:416px}
.hero-photo{position:absolute;inset:0;background:linear-gradient(180deg,#f3f3f3 0%,#ececec 70%,#d9d6d3 100%)}
.hero-people{position:absolute;left:250px;top:175px;width:300px;height:230px;border-radius:40% 40% 6px 6px;background:radial-gradient(ellipse at 50% 60%,#8aa0b8 0%,#b9c3cd 55%,rgba(236,236,236,0) 75%)}
.hero-title{position:absolute;top:64px;width:100%;text-align:center;font-family:"Courier Prime",monospace;font-size:23px;letter-spacing:1.5px;color:var(--pink)}
.divider{display:block;width:45px;height:1px;background:var(--ink);margin:0 auto}
.hero .divider{position:absolute;top:104px;left:344px}
.hero-sub{position:absolute;top:121px;width:100%;text-align:center;font-family:"Montserrat",sans-serif;font-weight:500;font-size:15.5px;line-height:23px;color:#1e1e1e}
.offer{position:absolute;top:416px;height:384px;width:366px;text-align:center}
.offer-left{left:0;background:var(--grey-bg)}
.offer-right{left:366px;width:367px;background:var(--pink-soft)}
.kicker{position:absolute;top:22px;width:100%;font-family:"Montserrat",sans-serif;font-size:9.5px;letter-spacing:1px;color:var(--grey-text)}
.offer-title{position:absolute;top:61px;width:100%;font-family:"Montserrat",sans-serif;font-weight:700;font-size:16px;letter-spacing:1.6px;color:var(--pink)}
.offer .divider{position:absolute;top:94px;left:160px}
.offer-lead{position:absolute;top:109px;width:100%;font-family:"Montserrat",sans-serif;font-weight:600;font-size:11px;line-height:15px;color:#444}
.offer-body{position:absolute;top:148px;width:100%;font-size:8.6px;line-height:16px;color:#444}
.offer-links{position:absolute;top:207px;width:100%;font-family:"Montserrat",sans-serif;font-size:8.4px;font-weight:600;letter-spacing:.5px}
.offer-links a{margin:0 9px;text-decoration:underline;color:#333}
.offer-links a.accent{color:var(--pink)}
.form-lead{position:absolute;top:239px;width:100%;font-family:"Montserrat",sans-serif;font-weight:600;font-size:11.5px;color:#666}
.guide-art{position:absolute;left:78px;top:108px;width:196px;height:144px;background:linear-gradient(160deg,#fbfbfb,#e4e1e3);transform:rotate(-3deg);box-shadow:0 2px 6px rgba(0,0,0,.15)}
.signup{position:absolute;top:262px;left:68px;width:227px}
.offer-right .signup{left:68px}
.field{display:flex;justify-content:space-between;align-items:center;height:27px;margin-bottom:3px;padding:0 9px;background:var(--white);border:1px solid var(--line);font-size:8px;color:#888}
.btn{display:block;width:100%;height:27px;border:0;margin-top:2px;font-family:"Montserrat",sans-serif;font-weight:700;font-size:8.6px;letter-spacing:.4px;color:var(--white);background:var(--pink)}
.btn-dark{background:var(--ink)}
.series{position:absolute;top:800px;left:0;width:733px;height:354px;text-align:center}
.series-photo{position:absolute;inset:0;background:linear-gradient(170deg,#fafafa 0%,#f1efee 55%,#e9e6e4 100%)}
.series-title{position:absolute;top:42px;width:100%;font-family:"Montserrat",sans-serif;font-weight:700;font-size:23px;letter-spacing:2px;color:var(--ink)}
.series .divider{position:absolute;top:82px;left:344px}
.series-text{position:absolute;width:100%;font-size:9.6px;line-height:18.5px;color:#333}
.series-text.strong{font-family:"Montserrat",sans-serif;font-weight:500;font-size:9.4px;line-height:18px;color:#444}
.series .btn{position:absolute;top:290px;left:253px;width:227px;margin:0}
.footer{position:absolute;top:1154px;left:0;width:733px;height:46px;background:var(--footer);color:var(--white);font-family:"Montserrat",sans-serif;font-size:8px}
.footer-legal{position:absolute;left:66px;top:19px}
.social{position:absolute;left:590px;top:17px;display:flex;gap:11px}
.social span{width:11px;height:11px;border-radius:50%;background:var(--white)}
.build-code{position:absolute;left:689px;top:20px;font-size:7px}
</style>
</head>
<body>
<div class="top-bar"></div>
<div class="menu-btn">
  <svg width="22" height="14" viewBox="0 0 22 14"><g fill="#fff"><rect width="22" height="2.5"/><rect y="5.7" width="22" height="2.5"/><rect y="11.5" width="22" height="2.5"/></g></svg>
</div>

<header class="hero">
  <div class="hero-photo" role="img" aria-label="Smiling couple sitting on the floor against a white wall with hand-drawn sketches of a window, lamp, framed picture, shelf and stool"></div>
  <div class="hero-people" role="img" aria-label="Young couple in denim looking upward"></div>
  <h1 class="hero-title">Brighten Every Day</h1>
  <span class="divider"></span>
  <p class="hero-sub">Chances are life is a little overwhelming.<br>Let us help</p>
</header>

<section class="offer offer-left">
  <p class="kicker">Baby Steps... (try out a few of our tricks)</p>
  <h2 class="offer-title">Swaps Email Series</h2>
  <span class="divider"></span>
  <p class="offer-lead">Save TIME, MONEY and SANITY<br>with simple product swaps.</p>
  <p class="offer-body">Reduce the amount of work it takes to run your home.<br>Swap out existing products for more sustainable ones.<br>Each swap saves you work, clutter, time &amp; money.</p>
  <p class="offer-links"><a class="accent">SEE SAMPLE SWAP</a><a>LEARN MORE</a></p>
  <p class="form-lead">Send your ideas my way..</p>
  <form class="signup">
    <div class="field">Name <svg width="7" height="8" viewBox="0 0 7 8"><circle cx="3.5" cy="2" r="2" fill="#999"/><path d="M0 8a3.5 3.5 0 0 1 7 0z" fill="#999"/></svg></div>
    <div class="field">Email: <svg width="9" height="7" viewBox="0 0 9 7"><rect width="9" height="7" fill="#999"/><path d="M0 0l4.5 3.5L9 0" stroke="#fff" fill="none"/></svg></div>
    <button class="btn" type="button">SEND ME THE GUIDE!</button>
  </form>
</section>

<section class="offer offer-right">
  <p class="kicker">Big Leap... (I'm ready to roll up my sleeves)</p>
  <h2 class="offer-title">Decluttering Guide</h2>
  <span class="divider"></span>
  <div class="guide-art" role="img" aria-label="Two printed guide pages fanned out"></div>
  <form class="signup">
    <div class="field">Name <svg width="7" height="8" viewBox="0 0 7 8"><circle cx="3.5" cy="2" r="2" fill="#999"/><path d="M0 8a3.5 3.5 0 0 1 7 0z" fill="#999"/></svg></div>
    <div class="field">Email: <svg width="9" height="7" viewBox="0 0 9 7"><rect width="9" height="7" fill="#999"/><path d="M0 0l4.5 3.5L9 0" stroke="#fff" fill="none"/></svg></div>
    <button class="btn btn-dark" type="button">SIGN ME UP!</button>
  </form>
</section>

<section class="series">
  <div class="series-photo" role="img" aria-label="Faded photo of a couple relaxing on the floor among moving boxes"></div>
  <h2 class="series-title">Swaps Email Series</h2>
  <span class="divider"></span>
  <p class="series-text" style="top:97px">Save TIME, MONEY and SANITY with simple product swaps.<br>And reduce the amount of work it takes to run your home.<br>Swap out existing products for more sustainable ones.<br>Each swap save you work, clutter, time &amp; money.</p>
  <p class="series-text" style="top:188px">You get an email 2x weekly for 6-12 weeks only<br>Get even more if you feel they are helpful to you</p>
  <p class="series-text strong" style="top:241px">Join our monthly SIMPLE SWAP SHARING web jams with other mums and get even<br>more ideas. Better yet, come with great tips of your own to share.</p>
  <button class="btn" type="button">SIGN ME UP!</button>
</section>

<footer class="footer">
  <p class="footer-legal">© 2018 All Rights Are Reserved.Terms of Use | Privacy Policy</p>
  <div class="social"><span></span><span></span><span></span><span></span></div>
  <span class="build-code">C4</span>
</footer>
</body>
</html>
```